One Thumbnail for Online Shop for PowerPoint Templates needed

We are selling PowerPoint Templates and need therefore a thumbnail for our online shop.

You can use a stock photo, mock-ups or other design elements.

Format:
squared like 500 x 500
or wide like 1280 x 720

If you want to use a title, use:

"Graphs" ---> Title
"PowerPoint template" ---> subtitle

Attachments:
- OLD: Our old thumbnail which I do not like
- Template: PowerPoint pictures which you can use ( you can also copy them if you need more than these)
- Example: Some examples I found from other shops (please do not copy them exactly, only to show what I mean)

I received lots of designs until now but many are not what I have expected

Target Market(s)

E-Commerce

Industry/Entity Type

Shop

Font styles to use
Sans Serif

Requirements
Should not have
• Do NOT re-design one of the template.png (these are only examples, I will replace them later)

```html
<!DOCTYPE html>
<html lang="en">
<head>
<meta charset="utf-8">
<title>Standard Graphs – SlideForge Presentation</title>
<link rel="stylesheet" href="https://fonts.googleapis.com/css2?family=Michroma&family=Jura:wght@300&family=Arimo:wght@400;700&display=swap">
<style>
  :root {
    --bg-deep: #23274f;
    --bg-mid: #3f4577;
    --bg-light: #6d6f9f;
    --slide-bg: #f7f9fb;
    --slide-ink: #1b1b1b;
    --slide-muted: #7a7f88;
    --bar-dark: #1f4d84;
    --bar-light: #4b86c6;
    --bar-bright: #3f8fdc;
    --title-ink: #ffffff;
  }
  * { margin: 0; padding: 0; box-sizing: border-box; }
  html, body { width: 1200px; height: 753px; overflow: hidden; background: var(--bg-deep); }
  .thumbnail { position: relative; width: 1200px; height: 753px; overflow: hidden; }
  .backdrop {
    position: absolute; inset: 0;
    background:
      radial-gradient(ellipse 60% 55% at 72% 38%, rgba(140,140,190,.55), transparent 70%),
      radial-gradient(ellipse 40% 60% at 12% 20%, rgba(90,95,140,.5), transparent 70%),
      linear-gradient(160deg, var(--bg-mid) 0%, var(--bg-light) 45%, var(--bg-deep) 100%);
  }
  .slide {
    position: absolute; left: 101px; width: 295px; height: 166px;
    background: var(--slide-bg);
    box-shadow: 0 4px 14px rgba(10,12,40,.35);
  }
  .slide svg { display: block; width: 100%; height: 100%; font-family: Arimo, Arial, sans-serif; }
  .slide--bars { top: 110px; }
  .slide--combo { top: 313px; }
  .slide--ranking { top: 514px; }
  .s-title { font-size: 9.5px; font-weight: 700; fill: var(--slide-ink); }
  .s-sub { font-size: 4.6px; fill: #444; }
  .s-label { font-size: 3.6px; font-weight: 700; fill: var(--slide-ink); }
  .s-tiny { font-size: 2.4px; fill: var(--slide-muted); }
  .s-body { font-size: 3.2px; fill: var(--slide-muted); }
  .s-val { font-size: 3.6px; fill: var(--slide-muted); }
  .s-val-in { font-size: 3.4px; fill: #fff; }
  .s-accent { font-size: 3.4px; fill: var(--bar-bright); }
  .heading {
    position: absolute; left: 458px; top: 478px;
    color: var(--title-ink);
    font-family: Michroma, "Arial Black", sans-serif;
    font-size: 64px; line-height: 78px; letter-spacing: 1px;
  }
  .subheading {
    position: absolute; left: 461px; top: 640px;
    color: var(--title-ink);
    font-family: Jura, Arial, sans-serif; font-weight: 300;
    font-size: 45px; letter-spacing: 2px; white-space: nowrap;
  }
</style>
</head>
<body>
<main class="thumbnail">
  <div class="backdrop" role="img" aria-label="Blue-tinted photo of a person working at a desktop computer in a bright office"></div>

  <section class="slide slide--bars">
    <svg viewBox="0 0 295 166">
      <text class="s-title" x="147" y="15" text-anchor="middle">Lorem ipsum dolor sit amet</text>
      <text class="s-sub" x="147" y="24" text-anchor="middle">Lorem ipsum dolor sit amet, consectetuer adipiscing elit. Aenean commodo ligula eget dolor.</text>
      <g class="chart-labels">
        <text class="s-label" x="21" y="41">Lorem ipsum</text><text class="s-tiny" x="21" y="45">Lorem ipsum dolor sit amet consectetur</text>
        <text class="s-label" x="115" y="41">Lorem ipsum</text><text class="s-tiny" x="115" y="45">Lorem ipsum dolor sit amet consectetur</text>
        <text class="s-label" x="21" y="102">Lorem ipsum</text><text class="s-tiny" x="21" y="106">Lorem ipsum dolor sit amet consectetur</text>
        <text class="s-label" x="115" y="102">Lorem ipsum</text><text class="s-tiny" x="115" y="106">Lorem ipsum dolor sit amet consectetur</text>
      </g>
      <g class="chart" transform="translate(28,88)">
        <line x1="0" y1="0" x2="80" y2="0" stroke="#ccc" stroke-width=".4"/>
        <g fill="var(--bar-dark)"><rect x="1" y="-8" width="4" height="8"/><rect x="8" y="-10" width="4" height="10"/><rect x="15" y="-12" width="4" height="12"/><rect x="22" y="-13" width="4" height="13"/><rect x="29" y="-11" width="4" height="11"/><rect x="36" y="-11" width="4" height="11"/><rect x="43" y="-10" width="4" height="10"/><rect x="50" y="-10" width="4" height="10"/><rect x="57" y="-9" width="4" height="9"/><rect x="64" y="-10" width="4" height="10"/><rect x="71" y="-9" width="4" height="9"/></g>
        <g fill="var(--bar-light)"><rect x="1" y="-20" width="4" height="12"/><rect x="8" y="-24" width="4" height="14"/><rect x="15" y="-31" width="4" height="19"/><rect x="22" y="-33" width="4" height="20"/><rect x="29" y="-28" width="4" height="17"/><rect x="36" y="-27" width="4" height="16"/><rect x="43" y="-27" width="4" height="17"/><rect x="50" y="-25" width="4" height="15"/><rect x="57" y="-22" width="4" height="13"/><rect x="64" y="-24" width="4" height="14"/><rect x="71" y="-21" width="4" height="12"/></g>
      </g>
      <g class="chart" transform="translate(122,88)">
        <line x1="0" y1="0" x2="80" y2="0" stroke="#ccc" stroke-width=".4"/>
        <g fill="var(--bar-dark)"><rect x="1" y="-9" width="4" height="9"/><rect x="8" y="-8" width="4" height="8"/><rect x="15" y="-11" width="4" height="11"/><rect x="22" y="-14" width="4" height="14"/><rect x="29" y="-12" width="4" height="12"/><rect x="36" y="-9" width="4" height="9"/><rect x="43" y="-10" width="4" height="10"/><rect x="50" y="-9" width="4" height="9"/><rect x="57" y="-11" width="4" height="11"/><rect x="64" y="-8" width="4" height="8"/><rect x="71" y="-9" width="4" height="9"/></g>
        <g fill="var(--bar-light)"><rect x="1" y="-19" width="4" height="10"/><rect x="8" y="-24" width="4" height="16"/><rect x="15" y="-23" width="4" height="12"/><rect x="22" y="-35" width="4" height="21"/><rect x="29" y="-30" width="4" height="18"/><rect x="36" y="-17" width="4" height="8"/><rect x="43" y="-22" width="4" height="12"/><rect x="50" y="-20" width="4" height="11"/><rect x="57" y="-24" width="4" height="13"/><rect x="64" y="-19" width="4" height="11"/><rect x="71" y="-21" width="4" height="12"/></g>
      </g>
      <g class="chart" transform="translate(28,148)">
        <line x1="0" y1="0" x2="80" y2="0" stroke="#ccc" stroke-width=".4"/>
        <g fill="var(--bar-dark)"><rect x="1" y="-9" width="4" height="9"/><rect x="8" y="-11" width="4" height="11"/><rect x="15" y="-10" width="4" height="10"/><rect x="22" y="-9" width="4" height="9"/><rect x="29" y="-11" width="4" height="11"/><rect x="36" y="-9" width="4" height="9"/><rect x="43" y="-10" width="4" height="10"/><rect x="50" y="-9" width="4" height="9"/><rect x="57" y="-10" width="4" height="10"/><rect x="64" y="-9" width="4" height="9"/><rect x="71" y="-9" width="4" height="9"/></g>
        <g fill="var(--bar-light)"><rect x="1" y="-19" width="4" height="10"/><rect x="8" y="-23" width="4" height="12"/><rect x="15" y="-19" width="4" height="9"/><rect x="22" y="-16" width="4" height="7"/><rect x="29" y="-22" width="4" height="11"/><rect x="36" y="-17" width="4" height="8"/><rect x="43" y="-18" width="4" height="8"/><rect x="50" y="-16" width="4" height="7"/><rect x="57" y="-18" width="4" height="8"/><rect x="64" y="-17" width="4" height="8"/><rect x="71" y="-16" width="4" height="7"/></g>
      </g>
      <g class="chart" transform="translate(122,148)">
        <line x1="0" y1="0" x2="80" y2="0" stroke="#ccc" stroke-width=".4"/>
        <g fill="var(--bar-dark)"><rect x="1" y="-9" width="4" height="9"/><rect x="8" y="-12" width="4" height="12"/><rect x="15" y="-14" width="4" height="14"/><rect x="22" y="-15" width="4" height="15"/><rect x="29" y="-13" width="4" height="13"/><rect x="36" y="-15" width="4" height="15"/><rect x="43" y="-16" width="4" height="16"/><rect x="50" y="-14" width="4" height="14"/><rect x="57" y="-13" width="4" height="13"/><rect x="64" y="-11" width="4" height="11"/><rect x="71" y="-12" width="4" height="12"/></g>
        <g fill="var(--bar-light)"><rect x="1" y="-17" width="4" height="8"/><rect x="8" y="-26" width="4" height="14"/><rect x="15" y="-32" width="4" height="18"/><rect x="22" y="-34" width="4" height="19"/><rect x="29" y="-27" width="4" height="14"/><rect x="36" y="-33" width="4" height="18"/><rect x="43" y="-34" width="4" height="18"/><rect x="50" y="-28" width="4" height="14"/><rect x="57" y="-26" width="4" height="13"/><rect x="64" y="-23" width="4" height="12"/><rect x="71" y="-25" width="4" height="13"/></g>
      </g>
      <g class="legend"><rect x="202" y="138" width="3" height="2" fill="var(--bar-light)"/><text class="s-tiny" x="207" y="140">Plan</text><rect x="202" y="143" width="3" height="2" fill="var(--bar-dark)"/><text class="s-tiny" x="207" y="145">Actual</text></g>
      <g class="bullets">
        <text class="s-body" x="224" y="58">• Lorem ipsum dolor sit amet,</text><text class="s-body" x="227" y="62">sed diam nonumy eirmod</text><text class="s-body" x="227" y="66">tempor invidunt ut labore</text><text class="s-body" x="227" y="70">et dolore magna aliquyam.</text>
        <text class="s-body" x="224" y="90">• Lorem ipsum dolor sit amet,</text><text class="s-body" x="227" y="94">sed diam nonumy eirmod</text><text class="s-body" x="227" y="98">tempor invidunt ut labore</text><text class="s-body" x="227" y="102">et dolore magna aliquyam.</text>
        <text class="s-body" x="224" y="124">• Lorem ipsum dolor sit amet,</text><text class="s-body" x="227" y="128">sed diam nonumy eirmod</text><text class="s-body" x="227" y="132">tempor invidunt ut labore</text>
      </g>
      <text class="s-tiny" x="283" y="161">31</text>
    </svg>
  </section>

  <section class="slide slide--combo">
    <svg viewBox="0 0 295 166">
      <text class="s-title" x="147" y="15" text-anchor="middle">Lorem ipsum dolor sit amet</text>
      <text class="s-sub" x="147" y="24" text-anchor="middle">Lorem ipsum dolor sit amet, consectetuer adipiscing elit. Aenean commodo ligula eget dolor.</text>
      <g class="bullets">
        <text class="s-body" x="14" y="69">• Lorem ipsum dolor sit amet,</text><text class="s-body" x="22" y="74">consetetur sadipscing elitr,</text><text class="s-body" x="22" y="79">sed diam nonumy eirmod</text><text class="s-body" x="22" y="84">tempor invidunt ut labore et</text><text class="s-body" x="22" y="89">dolore magna aliquyam erat,</text><text class="s-body" x="22" y="94">sed diam voluptua.</text>
        <text class="s-body" x="14" y="111">• Lorem ipsum dolor sit amet,</text><text class="s-body" x="22" y="116">consetetur sadipscing elitr,</text><text class="s-body" x="22" y="121">sed diam nonumy eirmod</text><text class="s-body" x="22" y="126">tempor invidunt ut labore et</text><text class="s-body" x="22" y="131">dolore magna aliquyam erat,</text><text class="s-body" x="22" y="136">sed diam voluptua.</text>
      </g>
      <g class="bars" fill="var(--bar-bright)">
        <rect x="91" y="115" width="9" height="31"/><rect x="104" y="112" width="9" height="34"/><rect x="118" y="105" width="9" height="41"/><rect x="131" y="96" width="9" height="50"/><rect x="145" y="93" width="9" height="53"/><rect x="158" y="88" width="9" height="58"/><rect x="171" y="84" width="9" height="62"/><rect x="185" y="79" width="9" height="67"/><rect x="198" y="76" width="9" height="70"/><rect x="212" y="72" width="9" height="74"/><rect x="225" y="69" width="9" height="77"/><rect x="238" y="64" width="9" height="82"/>
      </g>
      <g class="bar-values" text-anchor="middle">
        <text class="s-val-in" x="95.5" y="131">13</text><text class="s-val-in" x="108.5" y="129">14</text><text class="s-val-in" x="122.5" y="126">17</text><text class="s-val-in" x="135.5" y="121">21</text><text class="s-val-in" x="149.5" y="120">22</text><text class="s-val-in" x="162.5" y="117">24</text><text class="s-val-in" x="175.5" y="115">26</text><text class="s-val-in" x="189.5" y="113">28</text><text class="s-val-in" x="202.5" y="111">29</text><text class="s-val-in" x="216.5" y="109">31</text><text class="s-val-in" x="229.5" y="108">32</text><text class="s-val-in" x="242.5" y="105">34</text>
      </g>
      <polyline class="trend" fill="none" stroke="#9aa0a8" stroke-width=".6" points="95.5,102 108.5,100 122.5,94 135.5,85 149.5,83 162.5,79 175.5,74 189.5,68 202.5,68 216.5,64 229.5,60 242.5,60"/>
      <g class="trend-points" fill="#fff" stroke="#9aa0a8" stroke-width=".5">
        <circle cx="95.5" cy="102" r="1.2"/><circle cx="108.5" cy="100" r="1.2"/><circle cx="122.5" cy="94" r="1.2"/><circle cx="135.5" cy="85" r="1.2"/><circle cx="149.5" cy="83" r="1.2"/><circle cx="162.5" cy="79" r="1.2"/><circle cx="175.5" cy="74" r="1.2"/><circle cx="189.5" cy="68" r="1.2"/><circle cx="202.5" cy="68" r="1.2"/><circle cx="216.5" cy="64" r="1.2"/><circle cx="229.5" cy="60" r="1.2"/><circle cx="242.5" cy="60" r="1.2"/>
      </g>
      <g class="trend-values" text-anchor="middle">
        <text class="s-val" x="95.5" y="98">16</text><text class="s-val" x="108.5" y="96">17</text><text class="s-val" x="122.5" y="90">20</text><text class="s-val" x="135.5" y="81">24</text><text class="s-val" x="149.5" y="79">25</text><text class="s-val" x="162.5" y="75">27</text><text class="s-val" x="175.5" y="70">29</text><text class="s-val" x="189.5" y="64">32</text><text class="s-val" x="202.5" y="64">32</text><text class="s-val" x="216.5" y="60">34</text><text class="s-val" x="229.5" y="56">36</text><text class="s-val" x="242.5" y="56">36</text>
      </g>
      <text class="s-val" x="250" y="62">Lorem ipsum</text>
      <text class="s-accent" x="250" y="106">Lorem ipsum</text>
      <line x1="88" y1="146" x2="250" y2="146" stroke="#ccc" stroke-width=".4"/>
      <g class="axis" text-anchor="middle">
        <text class="s-val" x="95.5" y="154">Text</text><text class="s-val" x="108.5" y="154">Text</text><text class="s-val" x="122.5" y="154">Text</text><text class="s-val" x="135.5" y="154">Text</text><text class="s-val" x="149.5" y="154">Text</text><text class="s-val" x="162.5" y="154">Text</text><text class="s-val" x="175.5" y="154">Text</text><text class="s-val" x="189.5" y="154">Text</text><text class="s-val" x="202.5" y="154">Text</text><text class="s-val" x="216.5" y="154">Text</text><text class="s-val" x="229.5" y="154">Text</text><text class="s-val" x="242.5" y="154">Text</text>
      </g>
      <text class="s-tiny" x="276" y="161">34</text>
    </svg>
  </section>

  <section class="slide slide--ranking">
    <svg viewBox="0 0 295 166">
      <text class="s-title" x="147" y="15" text-anchor="middle">Lorem ipsum dolor sit amet</text>
      <text class="s-sub" x="147" y="24" text-anchor="middle">Lorem ipsum dolor sit amet, consectetuer adipiscing elit. Aenean commodo ligula eget dolor.</text>
      <text class="s-label" x="30" y="36">Lorem ipsum</text>
      <text class="s-body" x="30" y="41">Lorem ipsum dolor sit amet, consetetur sadipscing elitr, sed diam nonumy eirmod tempor</text>
      <text class="s-body" x="30" y="45">invidunt ut labore et dolore magna aliquyam erat, sed diam voluptua. At vero eos et accusam.</text>
      <g class="row-labels">
        <text class="s-val" x="19" y="60">Text</text><text class="s-val" x="19" y="68">Text</text><text class="s-val" x="19" y="76">Text</text><text class="s-val" x="19" y="85">Text</text><text class="s-val" x="19" y="93">Text</text><text class="s-val" x="19" y="101">Text</text><text class="s-val" x="19" y="109">Text</text><text class="s-val" x="19" y="117">Text</text><text class="s-val" x="19" y="125">Text</text><text class="s-val" x="19" y="133">Text</text>
      </g>
      <g class="rank-bars" fill="var(--bar-dark)">
        <rect x="32" y="57" width="79" height="4"/><rect x="32" y="65" width="74" height="4"/><rect x="32" y="73" width="74" height="4"/><rect x="32" y="82" width="66" height="4"/><rect x="32" y="90" width="61" height="4"/><rect x="32" y="98" width="56" height="4"/><rect x="32" y="106" width="54" height="4"/><rect x="32" y="114" width="43" height="4"/><rect x="32" y="122" width="36" height="4"/><rect x="32" y="130" width="33" height="4"/>
      </g>
      <g class="rank-values">
        <text class="s-val" x="113" y="60">31</text><text class="s-val" x="108" y="68">29</text><text class="s-val" x="108" y="76">29</text><text class="s-val" x="100" y="85">26</text><text class="s-val" x="95" y="93">24</text><text class="s-val" x="90" y="101">22</text><text class="s-val" x="88" y="109">21</text><text class="s-val" x="77" y="117">17</text><text class="s-val" x="70" y="125">14</text><text class="s-val" x="67" y="133">13</text>
      </g>
      <line x1="170" y1="54" x2="170" y2="136" stroke="#ccc" stroke-width=".4"/>
      <g class="change-bars" fill="var(--bar-light)">
        <rect x="170" y="57" width="18" height="4"/><rect x="170" y="65" width="24" height="4"/><rect x="158" y="73" width="12" height="4"/><rect x="164" y="82" width="6" height="4"/><rect x="170" y="90" width="18" height="4"/><rect x="170" y="98" width="18" height="4"/><rect x="170" y="106" width="6" height="4"/><rect x="164" y="114" width="6" height="4"/><rect x="170" y="122" width="24" height="4"/><rect x="170" y="130" width="12" height="4"/>
      </g>
      <g class="change-values">
        <text class="s-accent" x="190" y="60">+3%</text><text class="s-accent" x="196" y="68">+4%</text><text class="s-accent" x="148" y="76">-2%</text><text class="s-accent" x="154" y="85">-1%</text><text class="s-accent" x="190" y="93">+3%</text><text class="s-accent" x="190" y="101">+3%</text><text class="s-accent" x="178" y="109">+1%</text><text class="s-accent" x="154" y="117">-1%</text><text class="s-accent" x="196" y="125">+4%</text><text class="s-accent" x="184" y="133">+2%</text>
      </g>
      <g class="bullets">
        <text class="s-body" x="214" y="57">• Lorem ipsum dolor sit amet</text><text class="s-body" x="218" y="61">sed diam nonumy eirmod</text><text class="s-body" x="218" y="65">tempor invidunt ut labore</text><text class="s-body" x="218" y="69">et dolore magna aliquyam.</text>
        <text class="s-body" x="214" y="90">• Lorem ipsum dolor sit amet</text><text class="s-body" x="218" y="94">sed diam nonumy eirmod</text><text class="s-body" x="218" y="98">tempor invidunt ut labore</text><text class="s-body" x="218" y="102">et dolore magna aliquyam.</text>
        <text class="s-body" x="214" y="124">• Lorem ipsum dolor sit amet</text><text class="s-body" x="218" y="128">sed diam nonumy eirmod</text><text class="s-body" x="218" y="132">tempor invidunt ut labore</text><text class="s-body" x="218" y="136">et dolore magna aliquyam.</text>
      </g>
      <text class="s-tiny" x="276" y="161">35</text>
    </svg>
  </section>

  <h1 class="heading">Standard<br>Graphs</h1>
  <p class="subheading">SlideForge Presentation 1</p>
</main>
</body>
</html>
```